A private security company called "Tavron Security Services Ltd"

Hello everybody,

We need a web page for a company based in NZ. It is mainly an informative website so it would be wonderful if the designer puts their absolute best into making it a website that I would really appreciate. The website needs to show professionalism and also needs to make our web surfers find the information they need in a click. the company's colour is black and silver, and if those two colours could be integrated into the website it would be absolutely lovely. Please do contact me for any information.

Sincerely,
Dorian Vaskel

Industry/Entity Type

Security

```html
<!DOCTYPE html>
<html lang="en">
<head>
<meta charset="utf-8">
<title>Tavron Security Services Ltd</title>
<link href="https://fonts.googleapis.com/css2?family=Roboto:wght@300;400;500&display=swap" rel="stylesheet">
<style>
:root{
  --accent:#f5a623;
  --accent-light:#f9bd45;
  --ink:#222;
  --body:#4a4a4a;
  --slate:#3b3f47;
  --footer:#2e3138;
  --nav-top:#3a3a3a;
  --nav-bottom:#1c1c1c;
  --white:#fff;
}
*{margin:0;padding:0;box-sizing:border-box}
html,body{width:889px;height:1200px;overflow:hidden}
body{position:relative;font-family:'Roboto',sans-serif;color:var(--ink);background:var(--white)}
.abs{position:absolute}
.header{top:0;left:0;width:889px;height:94px}
.contact{top:50px;font-size:13px;display:flex;align-items:center;gap:8px;color:#333}
.brand{left:0;width:889px;top:42px;text-align:center;font-size:18px;font-weight:500;letter-spacing:2px;color:#111}
.brand small{display:block;font-size:8px;letter-spacing:1px;margin-top:2px}
.nav{top:94px;left:0;width:889px;height:46px;background:linear-gradient(var(--nav-top),var(--nav-bottom))}
.nav ul{list-style:none;display:flex;position:absolute;left:127px;top:0;height:46px}
.nav li{color:var(--white);font-size:11px;line-height:46px;padding:0 14px;border-right:1px solid #555}
.nav li:last-child{border-right:none}
.nav li.active{background:var(--accent);padding:0 17px}
.hero{top:140px;left:0;width:889px;height:383px;background:linear-gradient(120deg,#c9d8e8 0%,#eaf1f8 40%,#9fb3c9 75%,#6f8399 100%)}
.hero-title{left:135px;top:200px;font-size:23px;line-height:32px;color:#1b1b1b}
.btn{background:linear-gradient(var(--accent-light),var(--accent));color:var(--white);text-align:center;border-radius:2px}
.hero-btn{left:135px;top:271px;width:134px;height:37px;line-height:37px;font-size:15px}
.hero-arrows{left:288px;top:275px}
.section-title{left:128px;top:552px;font-size:15px;color:#333}
.pager{left:718px;top:552px;display:flex;gap:2px}
.pager span{width:16px;height:16px;background:var(--accent);display:block}
.card{top:588px;width:149px}
.card .photo{height:112px}
.card h3{margin-top:14px;font-size:12px;font-weight:400;color:var(--accent);text-align:center}
.card p{margin-top:6px;font-size:9.5px;line-height:15px;color:var(--body);text-align:center}
.welcome{top:788px;left:0;width:889px;height:208px;background:var(--slate)}
.welcome-photo{left:129px;top:34px;width:276px;height:142px;background:linear-gradient(110deg,#8fb3dc 0%,#d7e6f5 35%,#1e1f23 55%,#2c2e33 80%,#6f9fd3 100%)}
.welcome h2{left:422px;top:34px;font-size:16px;font-weight:400;color:var(--accent)}
.welcome .lead{left:424px;top:60px;font-size:11px;color:var(--white)}
.welcome .copy{left:422px;top:90px;width:339px;font-size:10px;line-height:18px;color:#e4e4e4}
.welcome-btn{left:675px;top:152px;width:86px;height:23px;line-height:23px;font-size:10px}
.col{top:1025px}
.col h4{font-size:10.5px;font-weight:400;color:#222;margin-bottom:14px}
.col li{list-style:none;font-size:10.5px;color:#222;height:20px;display:flex;align-items:center;gap:5px}
.footer{top:1134px;left:0;width:889px;height:66px;background:var(--footer)}
.footer .legal{left:130px;top:28px;font-size:10.5px;color:var(--white)}
.social{left:655px;top:20px;display:flex;gap:6px}
.social span{width:22px;height:22px;border-radius:50%;background:#444851;border:1px solid #565a63;display:block}
</style>
</head>
<body>
<header class="abs header">
  <div class="abs contact" style="left:128px">
    <svg width="20" height="14" viewBox="0 0 20 14"><rect width="20" height="14" rx="1" fill="var(--accent)"/><path d="M1 1l9 7 9-7" stroke="#fff" stroke-width="1.6" fill="none"/></svg>
    info@tavronsecurity.nz
  </div>
  <div class="abs brand">TAVRON<small>SECURITY SERVICES LTD.</small></div>
  <div class="abs contact" style="left:632px">
    <svg width="16" height="20" viewBox="0 0 16 20"><rect x="0" y="2" width="5" height="17" rx="1" fill="var(--accent)"/><rect x="6" y="0" width="10" height="19" rx="1" fill="none" stroke="var(--accent)" stroke-width="1.6"/><rect x="8" y="3" width="6" height="4" fill="var(--accent)"/></svg>
    +64-9-555-0142
  </div>
</header>

<nav class="abs nav">
  <ul>
    <li class="active">Home</li><li>Security Guards</li><li>Security Patrols</li><li>Access Control</li><li>TSS Security Careers</li><li>About Us</li><li>Contact Us</li>
  </ul>
</nav>

<section class="abs hero" role="img" aria-label="Photo of a CCTV security camera on a pole against a pale blue sky">
  <h1 class="abs hero-title" style="font-weight:400">PROFESSIONAL POWERFUL<br>SECURITY PROTECTION</h1>
  <div class="abs btn hero-btn">MORE INFO</div>
  <svg class="abs hero-arrows" width="44" height="30" viewBox="0 0 44 30"><path d="M14 2L2 15l12 13M30 2l12 13-12 13" stroke="#fff" stroke-width="1.5" fill="none"/><path d="M14 2L2 15l12 13" stroke="#556" stroke-width="1" fill="none" opacity=".5"/></svg>
</section>

<h2 class="abs section-title" style="font-weight:400">SERVICES WE PROVIDE</h2>
<div class="abs pager">
  <span><svg width="16" height="16"><path d="M10 4L6 8l4 4" stroke="#fff" stroke-width="1.5" fill="none"/></svg></span>
  <span><svg width="16" height="16"><path d="M6 4l4 4-4 4" stroke="#fff" stroke-width="1.5" fill="none"/></svg></span>
</div>

<div class="abs card" style="left:128px"><div class="photo" role="img" aria-label="Photo of a hand entering a code on a security keypad" style="background:linear-gradient(90deg,#bfc3c7,#4a4b50 60%,#d8d8da)"></div><h3>HOME SECURITY</h3><p>Mes cuml dia sed in lacus ut<br>eniascet ingerto aliiqt es site</p></div>
<div class="abs card" style="left:288px"><div class="photo" role="img" aria-label="Photo of two security officers in suits" style="background:linear-gradient(90deg,#3a3330,#8a6f62 50%,#2b2624)"></div><h3>BUSINESS SECURITY</h3><p>Mes cuml dia sed in lacus ut<br>eniascet ingerto aliiqt es site</p></div>
<div class="abs card" style="left:448px"><div class="photo" role="img" aria-label="Photo of a uniformed guard's belt with baton" style="background:linear-gradient(90deg,#c9b9a8,#6f8fb8 60%,#2e3a5a)"></div><h3>SECURITY FOR KIDS</h3><p>Mes cuml dia sed in lacus ut<br>eniascet ingerto aliiqt es site</p></div>
<div class="abs card" style="left:608px"><div class="photo" role="img" aria-label="Photo of armed security team in tactical gear" style="background:linear-gradient(90deg,#3d4a5c,#1f2228 50%,#52617a)"></div><h3>HARDWARE SYSTEM</h3><p>Mes cuml dia sed in lacus ut<br>eniascet ingerto aliiqt es site</p></div>

<section class="abs welcome">
  <div class="abs welcome-photo" role="img" aria-label="Photo of a security officer's back in a black uniform against a blue sky"></div>
  <h2 class="abs">WELCOME TO TSS</h2>
  <p class="abs lead">Mes cuml dia sed inenias ingerto lot aliiqtes dolore ipsum commete</p>
  <p class="abs copy">Mes cuml dia sed in lacus ut eniascet ingerto aliiqt es site amet eismod ictor ut ligulate ameti dapibus ticdu nt mtsen lusto dolor Itissim com. Mes cuml dia sed inertio lacusuei ascet dolingerto aliiqt sit amet eism com odictor ut ligulate cot.</p>
  <div class="abs btn welcome-btn">VIEW MORE</div>
</section>

<svg width="0" height="0" style="position:absolute"><defs><g id="tick"><circle cx="5" cy="5" r="5" fill="var(--accent)"/><path d="M2.6 5.2l1.7 1.7 3.2-3.4" stroke="#fff" stroke-width="1.3" fill="none"/></g></defs></svg>

<div class="abs col" style="left:128px"><h4>SECURITY GUARDS</h4><ul>
  <li><svg width="10" height="10"><use href="#tick"/></svg>Site Guards</li>
  <li><svg width="10" height="10"><use href="#tick"/></svg>Concierge Services</li>
  <li><svg width="10" height="10"><use href="#tick"/></svg>Corporate Events</li></ul></div>
<div class="abs col" style="left:293px"><h4>SECURITY PATROLS</h4><ul>
  <li><svg width="10" height="10"><use href="#tick"/></svg>Scheduled &amp; Random Patrols</li>
  <li><svg width="10" height="10"><use href="#tick"/></svg>Alarm Response</li></ul></div>
<div class="abs col" style="left:473px"><h4>ALARMS</h4><ul>
  <li><svg width="10" height="10"><use href="#tick"/></svg>Alarm Response</li>
  <li><svg width="10" height="10"><use href="#tick"/></svg>Alarm Monitoring</li>
  <li><svg width="10" height="10"><use href="#tick"/></svg>Alarm Installation</li></ul></div>
<div class="abs col" style="left:625px"><h4>ACCESS CONTROL SYSTEMS</h4><ul>
  <li><svg width="10" height="10"><use href="#tick"/></svg>Alarm Installation</li>
  <li><svg width="10" height="10"><use href="#tick"/></svg>Security Guards</li></ul></div>

<footer class="abs footer">
  <p class="abs legal">TSS © 2014 PRIVACY POLICY</p>
  <div class="abs social" aria-label="Social links"><span></span><span></span><span></span><span></span></div>
</footer>
</body>
</html>
```